WTF!!! We need a modern professional website for a business litigation law firm.

We need a modern, clean, professional and uncomplicated website for a new business trial and litigation law firm called "Haverlock Trial Firm PLLC". Website must be mobile optimized for iPad and smartphone. The law firm specializes in counseling and representing large corporations, small businesses and entrepreneurs in and out of the courtroom. Lawyers in the firm serve as Florida counsel and trial counsel to organizations facing claims involving product liability, premises liability, professional liability, vehicle and transportation liability, warranty claims, construction defects and delay claims, complex business disputes, commercial litigation and bid disputes in State and Federal Courts. The website is mainly to provide information about the firm, and should include sections describing the firm, identifying the Industries Served and Areas of Practice ," a separate page identifying the "Professionals", a separate page for "Resources & Advisories," and a traveling "Connect With Us" button a site visitor can click on that will launch an email to the Firm's general email account. The website should allow us to easily modify the content on these pages, and let us add/modify links to external information sources. We will not sell anything or take payments through the website. We do need to be able to easily upload and update photographs of attorneys and add new attorneys names/email hyperlinks as the firm grows. We would like to add developments in the law or success stories easily and quickly, such as through a blog page. On the "Connect With Us" page the website should have hyperlinks to email the Firm, and there should be hyperlinks to email each professional on the "Professionals" page. The website should be viewable on mobile devices without distortion. The law firm focuses on trial work and should have some imagery associated with courtrooms, but the overall theme of the site should be modern, clean, and communicate sophistication and strength. The website should be made in Wordpress. We have uploaded logo files for Haverlock Trial Firm.

Target Market(s)

Corporations and companies that are looking for legal representation. Other attorneys/legal industry.

Industry/Entity Type

Legal Industry

Coding

Coded - Design and coding required

Number of Pages Required

1 page

Font styles to use
Sans Serif

Requirements
Must have
• Simple, clean, sophisticated, modern website that includes the logo, watermark of logo, and the elements described above.
Nice to have
• Pictures of city scape, buildings, courtroom, team members.

```html
<!DOCTYPE html>
<html lang="en">
<head>
<meta charset="utf-8">
<title>Haverlock Trial Firm</title>
<link href="https://fonts.googleapis.com/css2?family=Cinzel:wght@400;500;600&family=Montserrat:ital,wght@0,400;0,500;0,600;0,700;1,400;1,500&display=swap" rel="stylesheet">
<style>
:root{
  --navy:#0f1d31;
  --black:#0b0b0b;
  --ink:#1b1b1b;
  --white:#ffffff;
  --mist:#ecedf1;
  --stone:#d9dadd;
  --card-dark:#262626;
  --gold:#f2b705;
  --serif:'Cinzel', serif;
  --sans:'Montserrat', sans-serif;
}
*{box-sizing:border-box;margin:0;padding:0}
html,body{width:1200px;height:5381px;overflow:hidden}
body{position:relative;background:var(--black);font-family:var(--sans);color:var(--ink)}
.abs{position:absolute}
a{color:inherit;text-decoration:none}

/* header */
.site-header{left:0;top:0;width:1200px;height:109px;background:var(--black)}
.brand{left:17px;top:30px;color:var(--white)}
.brand-name{font-size:26px;font-weight:700;letter-spacing:1px;line-height:1}
.brand-sub{font-size:10px;font-weight:600;letter-spacing:4px;margin-top:5px;padding-left:2px}
.main-nav a{position:absolute;top:43px;font-size:12px;color:#e9e9e9;font-weight:500;white-space:nowrap}
.main-nav a.active{font-weight:700;color:var(--white)}
.main-nav a.active::after{content:"";position:absolute;left:0;right:0;bottom:-6px;height:2px;background:var(--white)}
.btn-contact{left:1039px;top:29px;width:136px;height:44px;background:var(--white);border-radius:4px;box-shadow:3px 3px 0 #8a8f96;font-size:11.5px;font-weight:700;display:flex;align-items:center;justify-content:center;letter-spacing:.3px}

/* hero */
.hero{left:63px;top:109px;width:1137px;height:644px;border-top-left-radius:62px;overflow:hidden;background:
  radial-gradient(ellipse 240px 330px at 790px 300px,#3b5478 0%,rgba(59,84,120,.55) 45%,rgba(0,0,0,0) 100%),
  radial-gradient(ellipse 120px 120px at 790px 150px,#b58a70 0%,rgba(181,138,112,0) 100%),
  linear-gradient(95deg,#151617 0%,#2a2c30 30%,#4c5055 55%,#7b8087 75%,#2b2e33 100%)}
.hero-title{left:119px;top:256px;font-family:var(--serif);color:var(--white);font-size:40px;line-height:57px;letter-spacing:1px;font-weight:500;white-space:nowrap}
.hero-sub{left:118px;top:432px;color:#f0f0f0;font-style:italic;font-size:22px;line-height:38px}
.btn-outline{border:2px solid var(--white);border-radius:6px;color:var(--white);font-size:11.5px;font-weight:700;display:flex;align-items:center;justify-content:center;letter-spacing:.2px}
.hero-btn{left:117px;top:535px;width:174px;height:40px;background:#111;box-shadow:3px 3px 0 #6a6e74}
.dots span{position:absolute;left:1125px;width:16px;height:16px;border-radius:50%;border:1.5px solid #c9c9c9}
.dots span.on{background:var(--white);box-shadow:0 0 0 3px #444,0 0 0 4.5px #ddd}

/* about */
.about{left:63px;top:753px;width:1137px;height:992px;background:var(--white);border-top-left-radius:62px}
.about-h1{left:119px;top:868px;font-family:var(--serif);font-size:54px;font-weight:500;line-height:1;letter-spacing:1px}
.about-h2{left:121px;top:943px;font-family:var(--serif);font-size:36px;font-weight:500;line-height:1;letter-spacing:1px}
.about-rule{left:347px;top:866px;width:2px;height:112px;background:var(--ink)}
.about-lead{left:391px;top:866px;width:676px;font-size:17px;line-height:29px;color:#222}
.about-photo{left:123px;top:1020px;width:487px;height:554px;border-top-right-radius:62px;background:
  radial-gradient(ellipse 200px 140px at 210px 260px,#e9ecef 0%,rgba(233,236,239,0) 100%),
  linear-gradient(180deg,#c8ccd2 0%,#7a828d 35%,#2f3640 65%,#5a5f67 100%)}
.about-body{left:681px;top:1054px;width:415px;font-size:14.3px;line-height:25.1px;color:#333}
.btn-dark{background:var(--navy);color:var(--white);font-size:11.5px;font-weight:700;display:flex;align-items:center;justify-content:center;border-radius:4px;box-shadow:4px 4px 0 #000}
.about-btn{left:681px;top:1438px;width:168px;height:40px}
.callbar{left:560px;top:1525px;width:640px;height:80px;background:linear-gradient(90deg,#6a7480 0%,#a6adb5 45%,#e3e6e9 80%,rgba(255,255,255,0) 100%)}
.call-circle{left:516px;top:1522px;width:84px;height:84px;border-radius:50%;background:var(--navy);border:5px solid #cfd3d8;display:flex;align-items:center;justify-content:center}
.call-label{left:623px;top:1537px;color:var(--white);font-size:14px}
.call-num{left:623px;top:1559px;color:var(--white);font-size:24px;font-weight:700;letter-spacing:1.5px}

/* practice */
.practice{left:0;top:1745px;width:1200px;height:655px;background:var(--navy)}
.section-title{font-family:var(--serif);font-weight:500;letter-spacing:1.5px;text-align:center;left:0;width:1200px}
.practice-title{top:1849px;color:var(--white);font-size:41px}
.area-card{width:252px;height:114px;background:var(--white);border-radius:3px;text-align:center;padding-top:48px;box-shadow:0 4px 10px rgba(0,0,0,.3)}
.area-card.active{background:#111;color:var(--white);border:1px solid #555}
.area-card h3{font-size:15px;font-weight:700;line-height:20px;letter-spacing:.2px}
.area-card.two h3{margin-top:-12px}
.learn{display:inline-flex;align-items:center;gap:6px;font-size:9.5px;margin-top:6px;text-decoration:underline}
.learn svg{width:24px;height:18px}
.area-icon{width:70px;height:70px;border-radius:50%;background:var(--navy);border:4px solid var(--white);box-shadow:0 0 0 1.5px var(--navy);display:flex;align-items:center;justify-content:center}

/* resources */
.resources{left:0;top:2400px;width:1200px;height:620px;background:var(--mist)}
.res-title{left:109px;top:2522px;font-family:var(--serif);font-size:38px;font-weight:500;letter-spacing:1px;white-space:nowrap}
.res-sub{left:110px;top:2576px;font-family:var(--serif);font-size:21px;letter-spacing:.5px}
.res-body{left:109px;top:2630px;width:455px;font-size:15px;line-height:25px;color:#333}
.res-btn{left:109px;top:2861px;width:167px;height:42px}
.res-frame{left:667px;top:2535px;width:428px;height:366px;border:2px solid #2a2a2a;border-bottom-left-radius:70px}
.res-photo{left:690px;top:2508px;width:430px;height:372px;border-radius:4px;background:
  radial-gradient(ellipse 90px 170px at 130px 230px,#b4784a 0%,rgba(180,120,74,0) 100%),
  radial-gradient(ellipse 110px 190px at 290px 220px,#5f6671 0%,rgba(95,102,113,0) 100%),
  linear-gradient(120deg,#e4e1dc 0%,#cfcbc5 50%,#d8dadc 100%)}

/* professionals */
.pros{left:0;top:3020px;width:1200px;height:623px;background:var(--white)}
.pros-title{top:3119px;font-size:42px}
.pros-sub{top:3175px;font-size:21px}
.atty{width:215px;height:266px;top:3235px;overflow:hidden;box-shadow:0 3px 8px rgba(0,0,0,.2)}
.atty .pic{height:193px}
.atty .band{height:73px;background:var(--navy);color:var(--white);padding:14px 12px;position:relative}
.atty .name{font-size:13.5px;font-weight:700;white-space:nowrap}
.atty .role{font-size:12.5px;margin-top:3px;color:#dfe3e8}
.atty .ring{position:absolute;right:10px;top:20px;width:30px;height:30px;border-radius:50%;border:1.5px solid #fff}
.pros-btn{left:516px;top:3532px;width:167px;height:40px;font-size:11px}

/* stories */
.stories-navy{left:1000px;top:3643px;width:200px;height:632px;background:var(--navy)}
.stories{left:0;top:3643px;width:1135px;height:632px;background:var(--stone);border-bottom-right-radius:110px}
.stories-title{top:3722px;font-size:40px}
.stories-sub{top:3775px;font-size:21px}
.quote-card{left:111px;top:3829px;width:976px;height:324px;background:var(--card-dark)}
.quote-frame{left:146px;top:3858px;width:418px;height:343px;border:2px solid var(--white)}
.quote-photo{left:163px;top:3877px;width:416px;height:341px;background:
  radial-gradient(ellipse 220px 90px at 210px 290px,#d8d2c2 0%,rgba(216,210,194,0) 100%),
  linear-gradient(90deg,#8a8d7e 0%,#3a3f47 30%,#9c9a8a 55%,#2b3038 80%,#7d7d70 100%)}
.stars{left:620px;width:420px;top:3890px;text-align:center;color:var(--gold);font-size:22px;letter-spacing:3px}
.quote{left:620px;width:420px;top:3930px;text-align:center;color:var(--white);font-style:italic;font-size:15px;line-height:25px}
.cite{left:620px;width:420px;top:4067px;text-align:center;color:var(--white);font-size:13.5px;line-height:24px}
.arrow{font-size:26px;line-height:1}

/* contact */
.contact-navy{left:0;top:4275px;width:1200px;height:505px;background:var(--navy)}
.contact-black{left:0;top:4780px;width:1200px;height:260px;background:var(--black)}
.form-card{left:111px;top:4389px;width:405px;height:606px;background:#232323}
.form-title{left:140px;top:4406px;font-family:var(--serif);color:var(--white);font-size:36px;line-height:50px;letter-spacing:1px;white-space:nowrap}
.field{left:132px;width:359px;height:40px;background:var(--white);border-radius:3px 14px 14px 3px;display:flex;align-items:center;gap:14px;padding-left:14px;font-size:12.5px;color:#333}
.field.msg{height:171px;align-items:flex-start;padding-top:16px;border-radius:3px 3px 40px 3px}
.send-btn{left:226px;top:4911px;width:167px;height:40px;background:#232323}
.contact-title{left:583px;top:4400px;font-family:var(--serif);color:var(--white);font-size:36px;letter-spacing:1px}
.ci-icon{width:34px;height:34px;border-radius:50%;border:1.5px solid var(--white);display:flex;align-items:center;justify-content:center}
.ci-text{color:var(--white);font-size:11px;line-height:16px;white-space:nowrap}
.ci-text b{font-weight:600;font-size:12px}
.map{left:516px;top:4592px;width:571px;height:403px;background:linear-gradient(135deg,#eef0f2 0%,#dde0e4 50%,#eceef0 100%)}

/* footer */
.foot-brand{left:0;width:1200px;top:5090px;text-align:center;color:var(--white)}
.foot-brand .brand-name{font-size:42px}
.foot-brand .brand-sub{font-size:17px;letter-spacing:6px;margin-top:8px}
.foot-nav a{position:absolute;top:5255px;color:var(--white);font-size:12px;font-weight:600;white-space:nowrap}
.social{top:5245px;width:32px;height:32px;border-radius:50%;background:#2f3a4c;border:1.5px solid #8b95a5}
.copyright{left:0;width:1200px;top:5334px;text-align:center;color:#ddd;font-size:13px}
</style>
</head>
<body>

<header class="abs site-header">
  <div class="abs brand"><div class="brand-name">HAVERLOCK</div><div class="brand-sub">TRIAL FIRM</div></div>
  <nav class="main-nav">
    <a class="active" style="left:318px" href="#">Home</a>
    <a style="left:387px" href="#">About</a>
    <a style="left:452px" href="#">Industries Served &amp; Areas of Practice</a>
    <a style="left:709px" href="#">Professionals</a>
    <a style="left:819px" href="#">Resources &amp; Advisories</a>
    <a style="left:991px" href="#">Blog</a>
  </nav>
  <a class="abs btn-contact" href="#">CONTACT US</a>
</header>

<section>
  <div class="abs hero" role="img" aria-label="Confident attorney in a navy suit standing before dark city skyscrapers"></div>
  <h1 class="abs hero-title">STRENGTH IN ADVOCACY,<br>EXCELLENCE IN TRIAL<br>REPRESENTATION</h1>
  <p class="abs hero-sub">Counseling and representing businesses<br>in complex legal matters.</p>
  <a class="abs btn-outline hero-btn" href="#">CONNECT WITH US</a>
  <div class="dots"><span style="top:358px"></span><span class="on" style="top:385px"></span><span style="top:414px"></span><span style="top:447px"></span></div>
</section>

<section>
  <div class="abs about"></div>
  <h2 class="abs about-h1">ABOUT</h2>
  <div class="abs about-h2">THE FIRM</div>
  <div class="abs about-rule"></div>
  <p class="abs about-lead">Karspiciatis unde omnis iste natus error sit voluptatem accusantium doloremque laudantium, totam rem aperiam, eaque ipsa quae ab illo inventore veritatis et quasi architecto beatae vitae dicta sunt explicabo. Nemo enim ipsam voluptatem quia voluptas sit aspernatur aut.</p>
  <div class="abs about-photo" role="img" aria-label="Firm team meeting around a conference table with a laptop"></div>
  <p class="abs about-body">Jasefae aserspiciatis unde omnis iste natus error sit voluptatem accusantium doloremque laudantium, totam rem aperiam, eaque ipsa quaeab illo inventore veritatis et quasi architecto beatae vitae dicta sunt explicabo. Nemo enim ipsam voluptatem quseicsaea voluptas sit aspernatur aut odit aut fugit, sed csquia consequuntur magni dolores eos qusaei ratiosaene voluptatem sequi nesciunt. Neque porro quisquam est, qui dolorem ipsum quia dolor sisest amsaecet, consectetur, adipisci velit, sed quia non numquam eius modi tempora incidunt uset labore eset dolore magnam aliquam quaerat voluptatem. Utse enim ads minima veniam, quis nostrum exercitationem ullam corporis suscipit laboriosam.</p>
  <a class="abs btn-dark about-btn" href="#">LEARN MORE</a>
  <div class="abs callbar"></div>
  <div class="abs call-circle">
    <svg width="34" height="34" viewBox="0 0 24 24" fill="none" stroke="#fff" stroke-width="1.8" stroke-linecap="round" stroke-linejoin="round"><path d="M22 16.9v3a2 2 0 0 1-2.2 2 19.8 19.8 0 0 1-8.6-3.1 19.5 19.5 0 0 1-6-6A19.8 19.8 0 0 1 2.1 4.2 2 2 0 0 1 4.1 2h3a2 2 0 0 1 2 1.7c.1 1 .4 1.9.7 2.8a2 2 0 0 1-.5 2.1L8 9.9a16 16 0 0 0 6 6l1.3-1.3a2 2 0 0 1 2.1-.4c.9.3 1.8.6 2.8.7a2 2 0 0 1 1.7 2z"/></svg>
  </div>
  <div class="abs call-label">Call Us Now</div>
  <div class="abs call-num">888.888.8888</div>
</section>

<section>
  <div class="abs practice"></div>
  <h2 class="abs section-title practice-title">INDUSTRIES SERVED &amp; AREAS OF PRACTICE</h2>

  <div class="abs area-card" style="left:71px;top:1969px"><h3>PRODUCT LIABILITY</h3><a class="learn" href="#">Learn More <svg viewBox="0 0 24 18"><circle cx="16" cy="9" r="7" fill="none" stroke="currentColor"/><path d="M2 9h18M16 6l3 3-3 3" fill="none" stroke="currentColor"/></svg></a></div>
  <div class="abs area-card active" style="left:341px;top:1969px"><h3>PREMISES LIABILITY</h3><a class="learn" href="#">Learn More <svg viewBox="0 0 24 18"><circle cx="16" cy="9" r="7" fill="none" stroke="currentColor"/><path d="M2 9h18M16 6l3 3-3 3" fill="none" stroke="currentColor"/></svg></a></div>
  <div class="abs area-card" style="left:608px;top:1969px"><h3>PROFESSIONAL LIABILITY</h3><a class="learn" href="#">Learn More <svg viewBox="0 0 24 18"><circle cx="16" cy="9" r="7" fill="none" stroke="currentColor"/><path d="M2 9h18M16 6l3 3-3 3" fill="none" stroke="currentColor"/></svg></a></div>
  <div class="abs area-card two" style="left:878px;top:1969px"><h3>VEHICLE &amp;<br>TRANSPORTATION LIABILITY</h3><a class="learn" href="#">Learn More <svg viewBox="0 0 24 18"><circle cx="16" cy="9" r="7" fill="none" stroke="currentColor"/><path d="M2 9h18M16 6l3 3-3 3" fill="none" stroke="currentColor"/></svg></a></div>
  <div class="abs area-card" style="left:71px;top:2174px"><h3>WARRANTY CLAIMS</h3><a class="learn" href="#">Learn More <svg viewBox="0 0 24 18"><circle cx="16" cy="9" r="7" fill="none" stroke="currentColor"/><path d="M2 9h18M16 6l3 3-3 3" fill="none" stroke="currentColor"/></svg></a></div>
  <div class="abs area-card two" style="left:341px;top:2174px"><h3>CONSTRUCTION<br>DEFECTS &amp; DELAY CLAIMS</h3><a class="learn" href="#">Learn More <svg viewBox="0 0 24 18"><circle cx="16" cy="9" r="7" fill="none" stroke="currentColor"/><path d="M2 9h18M16 6l3 3-3 3" fill="none" stroke="currentColor"/></svg></a></div>
  <div class="abs area-card two" style="left:608px;top:2174px"><h3>COMPLEX BUSINESS<br>DISPUTES</h3><a class="learn" href="#">Learn More <svg viewBox="0 0 24 18"><circle cx="16" cy="9" r="7" fill="none" stroke="currentColor"/><path d="M2 9h18M16 6l3 3-3 3" fill="none" stroke="currentColor"/></svg></a></div>
  <div class="abs area-card two" style="left:878px;top:2174px"><h3>COMMERCIAL LITIGATION &amp;<br>BID DISPUTES</h3><a class="learn" href="#">Learn More <svg viewBox="0 0 24 18"><circle cx="16" cy="9" r="7" fill="none" stroke="currentColor"/><path d="M2 9h18M16 6l3 3-3 3" fill="none" stroke="currentColor"/></svg></a></div>

  <div class="abs area-icon" style="left:162px;top:1932px"><svg width="34" height="34" viewBox="0 0 24 24" fill="none" stroke="#fff" stroke-width="1.4"><path d="M3 8l9-4 9 4-9 4-9-4zM3 8v9l9 4 9-4V8M12 12v9"/></svg></div>
  <div class="abs area-icon" style="left:432px;top:1932px"><svg width="34" height="34" viewBox="0 0 24 24" fill="none" stroke="#fff" stroke-width="1.4"><path d="M3 21h18M5 21V9h14v12M3 9l2-5h14l2 5M9 21v-6h6v6M8 12h2M14 12h2"/></svg></div>
  <div class="abs area-icon" style="left:699px;top:1932px"><svg width="34" height="34" viewBox="0 0 24 24" fill="none" stroke="#fff" stroke-width="1.4"><circle cx="12" cy="9" r="6"/><circle cx="12" cy="9" r="3"/><path d="M8 14l-2 7 6-3 6 3-2-7"/></svg></div>
  <div class="abs area-icon" style="left:969px;top:1932px"><svg width="34" height="34" viewBox="0 0 24 24" fill="none" stroke="#fff" stroke-width="1.4"><path d="M2 7h12v9H2zM14 10h4l4 3v3h-8"/><circle cx="6" cy="18" r="2"/><circle cx="18" cy="18" r="2"/></svg></div>
  <div class="abs area-icon" style="left:162px;top:2137px"><svg width="34" height="34" viewBox="0 0 24 24" fill="none" stroke="#fff" stroke-width="1.4"><path d="M12 3l8 3v6c0 5-3.5 8-8 9-4.5-1-8-4-8-9V6z"/><path d="M8.5 12l2.5 2.5 4.5-5"/></svg></div>
  <div class="abs area-icon" style="left:432px;top:2137px"><svg width="34" height="34" viewBox="0 0 24 24" fill="none" stroke="#fff" stroke-width="1.4"><path d="M4 21V8l6-4v17M10 21V10h10v11M2 21h20M13 13h4M13 17h4"/></svg></div>
  <div class="abs area-icon" style="left:699px;top:2137px"><svg width="34" height="34" viewBox="0 0 24 24" fill="none" stroke="#fff" stroke-width="1.4"><circle cx="12" cy="12" r="8"/><circle cx="12" cy="12" r="3"/><path d="M12 4v5M12 15v5M4 12h5M15 12h5"/></svg></div>
  <div class="abs area-icon" style="left:969px;top:2137px"><svg width="34" height="34" viewBox="0 0 24 24" fill="none" stroke="#fff" stroke-width="1.4"><path d="M3 10l9-6 9 6M5 10v9M9.5 10v9M14.5 10v9M19 10v9M3 21h18"/></svg></div>
</section>

<section>
  <div class="abs resources"></div>
  <h2 class="abs res-title">RESOURCES &amp; ADVISORIES</h2>
  <div class="abs res-sub">LEGAL INSIGHTS &amp; UPDATES</div>
  <p class="abs res-body">Paerspiciatis unde omnis iste natus error asesit voluptatem accusantium doloremque laudantium, totam rem aperiam, eaque ipsa quae aaseb ilaslo inventore veritatis easet quasi architecto beatae vitae dictsaa sunt explicabo. Nemo enim ipsam voluptatem quia voluptas sit aspernatur aut odit aut fugit, sed quia consequuntur magni dolores eos qui ratione voluptatem sequi nesciunt. Neque porro quisquam est, qui dolorem.</p>
  <a class="abs btn-dark res-btn" href="#">LEARN MORE</a>
  <div class="abs res-frame"></div>
  <div class="abs res-photo" role="img" aria-label="Two attorneys standing with arms crossed in a bright office"></div>
</section>

<section>
  <div class="abs pros"></div>
  <h2 class="abs section-title pros-title">PROFESSIONALS</h2>
  <div class="abs section-title pros-sub">MEET OUR ATTORNEYS</div>

  <div class="abs atty" style="left:127px"><div class="pic" role="img" aria-label="Portrait of Daniel R. Whitcombe in a city street" style="background:linear-gradient(180deg,#bdb6a6 0%,#8a8c88 40%,#243654 75%,#1a2740 100%)"></div><div class="band"><div class="name">Daniel R. Whitcombe</div><div class="role">Ceo</div><span class="ring"></span></div></div>
  <div class="abs atty" style="left:378px"><div class="pic" role="img" aria-label="Portrait of Elena M. Castell in a courthouse hall" style="background:linear-gradient(180deg,#d4d7da 0%,#b3a58c 40%,#2b2f36 75%,#1c1f24 100%)"></div><div class="band"><div class="name">Elena M. Castell</div><div class="role">Lawyer</div><span class="ring"></span></div></div>
  <div class="abs atty" style="left:629px"><div class="pic" role="img" aria-label="Portrait of Marcus L. Oduya in an office" style="background:linear-gradient(180deg,#eef0f2 0%,#c8cbce 40%,#4a4f57 75%,#2e3238 100%)"></div><div class="band"><div class="name">Marcus L. Oduya</div><div class="role">Advisor</div><span class="ring"></span></div></div>
  <div class="abs atty" style="left:882px"><div class="pic" role="img" aria-label="Portrait of Priya S. Lindqvist in a law library" style="background:linear-gradient(90deg,#2f2c29 0%,#6e655a 35%,#e8e6e2 60%,#3a3835 100%)"></div><div class="band"><div class="name">Priya S. Lindqvist</div><div class="role">Member</div><span class="ring"></span></div></div>

  <a class="abs btn-dark pros-btn" href="#">VIEW ALL ATTORNEYS</a>
</section>

<section>
  <div class="abs stories-navy"></div>
  <div class="abs stories"></div>
  <h2 class="abs section-title stories-title">SUCCESS STORIES</h2>
  <div class="abs section-title stories-sub">WHAT OUR CLIENTS SAY</div>
  <div class="abs quote-card"></div>
  <div class="abs quote-frame"></div>
  <div class="abs quote-photo" role="img" aria-label="Attorney and client reviewing documents at a table"></div>
  <div class="abs stars">★★★★★</div>
  <p class="abs quote">"Jperspiciatis unde omnis iste natus error sit voluptatem accusantium doloremque laudantium, totam rem aperiam, eaque ipsa quae ab illo inventore veritatis et quasi architectos sit aspernatur."</p>
  <div class="abs cite">- JONAH<br>The Best!</div>
  <div class="abs arrow" style="left:1012px;top:4105px;color:#777">‹</div>
  <div class="abs arrow" style="left:1052px;top:4105px;color:#fff">›</div>
</section>

<section>
  <div class="abs contact-navy"></div>
  <div class="abs contact-black"></div>
  <div class="abs form-card"></div>
  <h2 class="abs form-title">REQUEST A FREE<br>CONSULTATION</h2>
  <div class="abs field" style="top:4531px"><svg width="14" height="14" viewBox="0 0 24 24" fill="#888"><circle cx="12" cy="8" r="5"/><path d="M3 22c0-5 4-8 9-8s9 3 9 8z"/></svg>Your Name</div>
  <div class="abs field" style="top:4590px"><svg width="14" height="14" viewBox="0 0 24 24" fill="none" stroke="#888" stroke-width="2"><rect x="3" y="5" width="18" height="14"/><path d="M3 6l9 7 9-7"/></svg>Email</div>
  <div class="abs field" style="top:4648px"><svg width="14" height="14" viewBox="0 0 24 24" fill="#888"><path d="M6.6 10.8a15 15 0 0 0 6.6 6.6l2.2-2.2c.3-.3.7-.4 1-.2 1.1.4 2.3.6 3.6.6.6 0 1 .4 1 1V20c0 .6-.4 1-1 1A17 17 0 0 1 3 4c0-.6.4-1 1-1h3.5c.6 0 1 .4 1 1 0 1.3.2 2.5.6 3.6.1.3 0 .7-.2 1z"/></svg>Phone Number</div>
  <div class="abs field msg" style="top:4709px"><svg width="16" height="14" viewBox="0 0 24 24" fill="#888"><path d="M3 4h14v10H8l-5 4z"/><path d="M19 8h2v10l-4-3h-7v-1h9z"/></svg>Write &nbsp;A Message</div>
  <a class="abs btn-outline send-btn" href="#">SEND MESSAGE</a>

  <h2 class="abs contact-title">CONTACT US</h2>
  <div class="abs ci-icon" style="left:580px;top:4470px"><svg width="16" height="16" viewBox="0 0 24 24" fill="#fff"><path d="M6.6 10.8a15 15 0 0 0 6.6 6.6l2.2-2.2c.3-.3.7-.4 1-.2 1.1.4 2.3.6 3.6.6.6 0 1 .4 1 1V20c0 .6-.4 1-1 1A17 17 0 0 1 3 4c0-.6.4-1 1-1h3.5c.6 0 1 .4 1 1 0 1.3.2 2.5.6 3.6.1.3 0 .7-.2 1z"/></svg></div>
  <div class="abs ci-text" style="left:627px;top:4470px">Call Us<br><b>888.888.8888</b></div>
  <div class="abs ci-icon" style="left:760px;top:4470px"><svg width="16" height="16" viewBox="0 0 24 24" fill="none" stroke="#fff" stroke-width="2"><rect x="3" y="5" width="18" height="14"/><path d="M3 6l9 7 9-7"/></svg></div>
  <div class="abs ci-text" style="left:807px;top:4470px">Email<br><b>info@haverlocktrialfirm.com</b></div>
  <div class="abs" style="left:588px;top:4528px"><svg width="18" height="22" viewBox="0 0 24 28" fill="#fff"><path d="M12 0a9 9 0 0 0-9 9c0 7 9 17 9 17s9-10 9-17a9 9 0 0 0-9-9zm0 13a4 4 0 1 1 0-8 4 4 0 0 1 0 8z"/></svg></div>
  <div class="abs ci-text" style="left:627px;top:4527px">Office Locations<br><b>120 Meridian Ave, Suite 200, Tampa, FL 33602</b></div>
  <div class="abs arrow" style="left:982px;top:4528px;color:#8a93a0">‹</div>
  <div class="abs arrow" style="left:1022px;top:4528px;color:#fff">›</div>
  <div class="abs map" role="img" aria-label="Street map marking the firm's office location"></div>
</section>

<footer>
  <div class="abs foot-brand"><div class="brand-name">HAVERLOCK</div><div class="brand-sub">TRIAL FIRM</div></div>
  <nav class="foot-nav">
    <a style="left:119px" href="#">Home</a>
    <a style="left:183px" href="#">About</a>
    <a style="left:246px" href="#">Industries Served &amp; Areas of Practice</a>
    <a style="left:503px" href="#">Professionals</a>
    <a style="left:612px" href="#">Resources &amp; Advisories</a>
    <a style="left:784px" href="#">Blog</a>
    <a style="left:838px" href="#">Contact Us</a>
  </nav>
  <span class="abs social" style="left:937px" aria-label="Social link"></span>
  <span class="abs social" style="left:997px" aria-label="Social link"></span>
  <span class="abs social" style="left:1056px" aria-label="Social link"></span>
  <div class="abs copyright">©2025. All rights reserved.</div>
</footer>

</body>
</html>
```